IT Company needs Website for new Web and Mobile products for Sports and Fitness

Background:

We developed web based white label frontend web solution, backend services and white label mobile apps for to log, analyze, share and control sport and fitness activities. The name of this product suite is "Trevantix" (http://trevantix-example.com)

This products will be used by customers that provide platforms and community systems for sport and fitness. One of the major USP's is, that our technology i open for nearly all common formats, devices and apps out in the market. This means, you can just upload your data directly from device, file or app - e.G. Nerovo, Bolvane, Ravelo, StrideVault, Pacelumo, Zembra and much others.

Two current concrete examples/References

(1) MyQuorel
It's an international platform from quorel for runners. It provides individual training lans and a training log. MyQuorel uses the Backend Product "Trevantix Hub" (see http://hub.trevantix-example.net for a landing page) to integrate device, file and app support. Before this, every user has to track his training with manual inputs

(2) Paceharbor and fen-zine
Both are German customers. Paceharor is focused on runners. fen-zine is focused on Triatheletes. Both use the Product "Trevantix Web". This is a complete web solution with web based frontend solutions for athletes and coaches.

What do we need?
We need website layout for B2B for our products. We don't need lot's of pages. We need the pretty and nice layout, so we can derive the pages we need.

IMPORTANT
We don't talk about the webpages for the product itself (this will be a different project in future). We talk about a website, explaining the products)
Updates

Hi all,

we just start reviewing the first designs, and try to give feedback as detailed as possible. We attached a PDF document, to describe the the products a little bit more detailed. 

As written in the description, in the end we have two different sections. One is the usual stuff like "start page", "about", "contact", "disclaimer", "pricing", "blah...." and one will be the Developer Section, the "Tec Section". This ist aimed to developers (of our customers) that will integrate our products in there existing system or which will integrate our services in there own software.  This "pages" are more like "documentation", so easy to read and cool to look at (cause developers likes it cool, but straight)

Dear all,

we just do the final review. Cause this week is with heavy load, it takes some time...

Cheers

Odell

Target Market(s)

* Platforms and Communities for sport, health and fitness
* Gyms

Industry/Entity Type

Concrete

Font styles to use
Sans Serif

Requirements
Must have
• * Templates shall base on bootstrap. If not, it shall be easily realized on our site with bootstrap or out of the box "full responsive"

* HTML5 / CSS3
Nice to have
• PAGES
- Start Page
- Generic Template (from which we can derive additional pages)
- Contact Page
- Disclaimer Page
- Blog/News Page
- "About us" Page (can be combined with disclaimer)
- One Example product page (in end we have 3 products), shall show (if you need product details, let me know)
- product and it's description
- pricing information
- Add-Ons for the product
- Developer Section Page (Start Point for developers, where the finde "basic technical concepts and developer API's
- Example Developer Page for technical concept
- Example Developer Page for API

LOGO ISSUE
You can use an align to the Logo attached OR provide a new logo. The given logo is a logo for our own B2C Website http://trevantix-example.net. It's not really necessary, that the logo or the color must be used for the product website. Maybe it will be better if it's a complete new one, to avoid irritation between Trevantix as a B2B product and trevantix-example.net as a B2C platform.
Should not have
• No Flash and other proprietary technologies

```html
<!DOCTYPE html>
<html lang="en">
<head>
<meta charset="utf-8">
<title>Trevantix</title>
<link href="https://fonts.googleapis.com/css2?family=Oswald:wght@400;500&family=Source+Sans+3:ital,wght@0,400;0,600;1,400&display=swap" rel="stylesheet">
<style>
:root{
  --orange:#e8730c;
  --dark:#3a3a3a;
  --text:#555;
  --bubble:#eef0f3;
  --footer:#111;
  --fb:#3b5a9a;--tw:#2d9fd9;--rss:#f26c1b;--yt:#d62d2d;
}
*{box-sizing:border-box;margin:0;padding:0}
html,body{width:902px;height:1200px;overflow:hidden;background:#fff}
body{font-family:"Source Sans 3",sans-serif;color:var(--text);position:relative}
.page{position:relative;width:902px;height:1200px}
.brand{position:absolute;left:65px;top:34px;display:flex;align-items:center;gap:10px}
.brand-mark{width:34px;height:34px;background:var(--orange);border-radius:50%}
.brand-name{font-size:38px;font-weight:600;color:var(--orange);letter-spacing:.5px;line-height:44px}
.top-links{position:absolute;right:67px;top:51px;font-size:12.5px;color:#333}
.top-links span{margin:0 8px;color:#333}
.main-nav{position:absolute;left:65px;top:104px;width:771px;height:38px;background:var(--orange);display:flex;align-items:center}
.main-nav a{font-family:"Oswald",sans-serif;font-size:14px;color:#fff;text-decoration:none;margin-left:17px;margin-right:25px;letter-spacing:.2px}
.search{position:absolute;right:7px;top:6px;width:168px;height:26px;background:#fff;font-size:10px;font-style:italic;color:#aaa;padding:6px 8px}
.search svg{position:absolute;right:8px;top:7px}
.hero{position:absolute;left:65px;top:142px;width:771px;height:321px;overflow:hidden}
.hero-photo{position:absolute;inset:0;background:linear-gradient(100deg,#8aa8c6 0%,#5f86b4 45%,#7e94aa 70%,#b2a38d 100%)}
.hero-title{position:absolute;left:389px;top:88px;font-family:"Oswald",sans-serif;font-weight:500;font-size:26px;line-height:34px;color:#fff;letter-spacing:.3px;white-space:nowrap}
.hero-copy{position:absolute;left:389px;top:127px;width:350px;font-size:12.5px;line-height:19px;color:#fff}
.dots{position:absolute;right:22px;top:292px;display:flex;gap:1px}
.dots i{width:9px;height:9px;border:1.5px solid #fff;border-radius:50%;display:block}
.dots i.on{background:#fff}
.features{position:absolute;left:65px;top:504px;width:771px;height:80px}
.feature{position:absolute;top:0;text-align:center;transform:translateX(-50%)}
.feature .circle{width:50px;height:50px;border-radius:50%;background:var(--dark);margin:0 auto;display:flex;align-items:center;justify-content:center}
.feature p{font-size:18px;color:#333;margin-top:9px;white-space:nowrap}
.divider{position:absolute;left:65px;width:771px;height:14px;background:radial-gradient(ellipse at top,rgba(0,0,0,.09),rgba(0,0,0,0) 70%)}
.welcome h2{position:absolute;top:660px;width:902px;text-align:center;font-weight:400;font-size:23px;color:var(--orange)}
.welcome p{position:absolute;left:62px;top:701px;width:782px;text-align:center;font-size:11.3px;line-height:20px;color:#444}
.section-title{position:absolute;font-weight:400;font-size:20px;color:var(--orange)}
.about-media{position:absolute;left:70px;top:835px;width:161px;height:150px;background:linear-gradient(180deg,#6b6b5d 0%,#475040 45%,#323a2f 100%)}
.play{position:absolute;left:56px;top:54px;width:40px;height:40px;border-radius:50%;background:#111;border:2px solid #fff;display:flex;align-items:center;justify-content:center}
.about-text{position:absolute;left:253px;top:830px;width:330px;font-size:10.5px;line-height:17px;color:#444}
.about-list{list-style:none;margin-top:6px}
.about-list li{position:relative;padding-left:19px;margin-bottom:5px}
.about-list li:before{content:"";position:absolute;left:0;top:4px;width:9px;height:9px;border-radius:50%;background:#777}
.about-list li:after{content:"";position:absolute;left:3px;top:6.5px;border-left:4px solid #fff;border-top:2px solid transparent;border-bottom:2px solid transparent}
.quote{position:absolute;left:616px;top:834px;width:219px;height:91px;background:var(--bubble);padding:12px 8px 0 15px;font-size:10px;line-height:18px;font-style:italic;color:#555}
.quote:after{content:"";position:absolute;left:150px;bottom:-18px;border-top:18px solid var(--bubble);border-left:28px solid transparent}
.quote b{position:absolute;left:5px;top:2px;font-size:16px;color:#bbb;font-style:normal}
.avatar{position:absolute;left:637px;top:938px;width:40px;height:40px;border-radius:50%;background:linear-gradient(#6a4a38,#e7cdbd)}
.t-name{position:absolute;left:713px;top:947px;font-size:10px;font-weight:600;color:#333}
.t-role{position:absolute;left:713px;top:968px;font-size:10px;font-weight:600;color:#333;display:flex;align-items:center;gap:6px}
.partners{position:absolute;left:80px;top:1062px;width:742px;display:flex;justify-content:space-between;align-items:center}
.partners span{font-size:14px;font-weight:600;color:var(--orange)}
.site-footer{position:absolute;left:0;top:1114px;width:902px;height:86px;background:var(--footer);color:#eee}
.site-footer .links{position:absolute;left:70px;top:22px;font-size:10.5px}
.site-footer .copy{position:absolute;left:70px;top:47px;font-size:10.5px}
.social{position:absolute;left:704px;top:24px;display:flex;gap:10px}
.social i{display:block;width:27px;height:27px}
</style>
</head>
<body>
<div class="page">
  <header>
    <div class="brand"><span class="brand-mark"></span><span class="brand-name">Trevantix</span></div>
    <nav class="top-links">Manual<span>|</span>My Sport<span>|</span>Login</nav>
    <nav class="main-nav">
      <a>HOME</a><a>ABOUT US</a><a>SERVICES</a><a>NEWS</a><a>SUPPORT</a><a>CONTACT</a>
      <div class="search">Search..
        <svg width="11" height="11" viewBox="0 0 11 11"><circle cx="4.5" cy="4.5" r="3.5" fill="none" stroke="#999" stroke-width="1.5"/><line x1="7" y1="7" x2="10" y2="10" stroke="#999" stroke-width="1.5"/></svg>
      </div>
    </nav>
  </header>

  <section class="hero">
    <div class="hero-photo" role="img" aria-label="Hands holding a tablet showing a treadmill runner and activity chart, with a blurred runner against a blue sky behind"></div>
    <h1 class="hero-title">DUIS AUTEM VEL EUM IRURE DOLOR</h1>
    <p class="hero-copy">Jerta baditaut onsequser untur magni dolores eoquie voluptate msequi nesciunt. Voluptatem accusantium dolorem lorem.</p>
    <div class="dots"><i class="on"></i><i></i><i></i><i></i></div>
  </section>

  <section class="features">
    <div class="feature" style="left:38px">
      <div class="circle"><svg width="24" height="24" viewBox="0 0 24 24"><path d="M13 4a8 8 0 1 0 0 16" fill="none" stroke="var(--orange)" stroke-width="3"/><path d="M9 12h12M17 8l4 4-4 4" fill="none" stroke="var(--orange)" stroke-width="3"/></svg></div><p>Log</p></div>
    <div class="feature" style="left:197px">
      <div class="circle"><svg width="24" height="24" viewBox="0 0 24 24"><rect x="3" y="14" width="4" height="7" fill="var(--orange)"/><rect x="9" y="10" width="4" height="11" fill="var(--orange)"/><rect x="15" y="12" width="4" height="9" fill="var(--orange)"/><path d="M3 11l6-5 5 3 7-6" fill="none" stroke="var(--orange)" stroke-width="2"/></svg></div><p>Analyze</p></div>
    <div class="feature" style="left:368px">
      <div class="circle"><svg width="24" height="24" viewBox="0 0 24 24"><line x1="6" y1="12" x2="18" y2="5" stroke="var(--orange)" stroke-width="2"/><line x1="6" y1="12" x2="18" y2="19" stroke="var(--orange)" stroke-width="2"/><circle cx="6" cy="12" r="3.5" fill="var(--orange)"/><circle cx="18" cy="5" r="3" fill="var(--orange)"/><circle cx="18" cy="19" r="3" fill="var(--orange)"/></svg></div><p>Share</p></div>
    <div class="feature" style="left:534px">
      <div class="circle"><svg width="24" height="24" viewBox="0 0 24 24"><path d="M4 20l6-6 3 3 7-11M15 6h5v5" fill="none" stroke="var(--orange)" stroke-width="3"/></svg></div><p>Control Sport</p></div>
    <div class="feature" style="left:709px">
      <div class="circle"><svg width="26" height="26" viewBox="0 0 26 26"><g stroke="var(--orange)" stroke-width="4"><line x1="13" y1="2" x2="13" y2="24"/><line x1="2" y1="13" x2="24" y2="13"/><line x1="5" y1="5" x2="21" y2="21"/><line x1="21" y1="5" x2="5" y2="21"/></g><circle cx="13" cy="13" r="7" fill="var(--orange)"/><circle cx="13" cy="13" r="3" fill="var(--dark)"/></svg></div><p>Fitness Activities</p></div>
  </section>

  <div class="divider" style="top:622px"></div>

  <section class="welcome">
    <h2>Welcome To Our Website</h2>
    <p>Atincidunt urna nec mollis. Mauris in sem felisty sed feugiat justo. Sed malesuada ullamcooyrpe sem a mattis. Nunc molestie arcu coryj linvallist lectus malesuada a non sodales. Aliquam erat volutpat. Aenean arcu mauris semper vel sagittis at blandit eu sapien. Crastill quis massa ante ut lucitus orci. Lorem ipsum dolor sit a met consectetur adipisti phasellus commodo turpis.&nbsp; Typi non habent claritatem insitam; est usus legentis in iis qui facit eorum&nbsp; Investigationes dem</p>
  </section>

  <section class="about">
    <h3 class="section-title" style="left:70px;top:788px">About Us</h3>
    <div class="about-media" role="img" aria-label="Video still of a runner's legs on a grass path">
      <div class="play"><svg width="14" height="16" viewBox="0 0 14 16"><path d="M2 1l11 7-11 7z" fill="#fff"/></svg></div>
    </div>
    <div class="about-text">
      <p>Mit trevantix-example.net kannst du deinen Sport festhalten, auswerten, teilen, dich motivieren und coachen lassen. Nutze einfach deine Lieblings-App,deinen bevorzugten Sportcomputer oder trage manuell ein. Trevantix begleitet, fördert und motiviert dich dein gesamtes Sportlerleben.</p>
      <ul class="about-list">
        <li>unterstützt mehr als 100 Sportarten</li>
        <li>versteht Geräte, Apps und Formate</li>
        <li>motiviert mit einzigartigen Events</li>
        <li>bringt Sportler vor Ort zusammen</li>
      </ul>
    </div>
  </section>

  <section class="testimonials">
    <h3 class="section-title" style="left:616px;top:788px">Testimonials</h3>
    <blockquote class="quote"><b>“</b>Fusce feugiat malesuada odio. Morbi nunc do gravida&nbsp; at, cursus nec, luctus a, lorem. Maecn as tristique orci acd sem. Lorem ipsum dolorsi t amet, consectetur adipisicing elit ”</blockquote>
    <div class="avatar" role="img" aria-label="Portrait of the reviewer"></div>
    <div class="t-name">Maecenintty interucoqt</div>
    <div class="t-role"><svg width="12" height="11" viewBox="0 0 12 11"><circle cx="6" cy="3" r="3" fill="#444"/><path d="M0 11c0-4 3-5 6-5s6 1 6 5z" fill="#444"/></svg>Dara Quill's</div>
  </section>

  <div class="divider" style="top:1030px"></div>

  <section class="partners">
    <span>Nerovo</span><span>Bolvane</span><span>Ambrith</span><span>Halvix</span><span>Morisa</span><span>Quillen</span><span>Tarnok</span><span>Dravo</span><span>Routewell</span><span>Swerin</span><span>Pelko</span>
  </section>

  <footer class="site-footer">
    <div class="links">Home | About Us | Services | News | Support | Contact</div>
    <div class="copy">Copyrights 2013. All Rights Reserved.</div>
    <div class="social">
      <i style="background:var(--fb)" aria-label="Social link 1"></i>
      <i style="background:var(--tw)" aria-label="Social link 2"></i>
      <i style="background:var(--rss)" aria-label="Feed link"></i>
      <i style="background:var(--yt)" aria-label="Video link"></i>
    </div>
  </footer>
</div>
</body>
</html>
```